tinyTally Resource Book - 10 maths tasks to do outside

I need a 22 (11 pages back to back) page A6 sized book produced to standard for submission to professional printer. Needs to be as .pdf file showing guide lines and allowances for colour bleed. I have text already written and submitted as attachment in a Word file with margins set to A6 size. The theme of the materials is "Nature Play" so using lots of pictures from nature (Australia preferably) and showing lots of patterns in nature (rocks, leaves, flower petals etc). Some of the tasks refer to specific activities, such as "shadows" and "floating" so would be great to illustrate appropriately. The big emphasis is on learning outside the classroom, getting kids to engage actively with nature. I would like to see the pages as full colour - so not white background. The book itself will be spiral bound along the top edge so a margin of at least 1cm will be required at the top of each page (or the bottom of even numbered pages). Book will be printed on plastic laminated matte paper for outdoor use. Font size needs to be big enough to read. Fonts sizes, alignments and page numbers are all different at the moment and need to be standardised. One photo is included in a page as a sample if you can use it, otherwise disregard. Logo for Wattlebrook Numeracy Guild is also included to have as part of the acknowledgements at the back of the book.

Target Market(s)

Book is for early childhood and preschool teachers.

Industry/Entity Type

Education

Font styles to use
Sans Serif

Requirements
Must have
• Colour and appeal.
Nice to have
• Use of natural colours instead of bright catchy colours but that is your call.
Should not have
• American spelling

```html
<!DOCTYPE html>
<html lang="en-AU">
<head>
<meta charset="utf-8">
<title>Big Bigger Biggest – tinyTally task card</title>
<link rel="stylesheet" href="https://fonts.googleapis.com/css2?family=Nunito:wght@900&family=Open+Sans:ital,wght@1,800&family=Didact+Gothic&display=swap">
<style>
  :root {
    --navy: #2b3a8f;
    --heading-blue: #2e3192;
    --ink: #111111;
    --diamond-red: #d7282f;
    --sky: #6d9cc6;
    --sea: #a7c3da;
    --haze: #d6dadb;
    --sand-light: #dccbb0;
    --sand-dark: #c6aa86;
    --halo: #ffffff;
  }
  * { margin: 0; padding: 0; box-sizing: border-box; }
  html, body { width: 848px; height: 1200px; overflow: hidden; background: #ffffff; }
  .task-card {
    position: relative;
    width: 848px;
    height: 1200px;
    overflow: hidden;
  }
  .beach-backdrop {
    position: absolute;
    inset: 0;
    background: linear-gradient(180deg,
      var(--sky) 0%,
      var(--sea) 22%,
      var(--haze) 36%,
      var(--sand-light) 48%,
      var(--sand-light) 70%,
      var(--sand-dark) 100%);
  }
  .stone-stack {
    position: absolute;
    left: 500px;
    top: 590px;
    width: 330px;
    height: 330px;
    border-radius: 50%;
    background: radial-gradient(ellipse at 50% 55%, rgba(245,242,236,0.75) 0%, rgba(230,225,215,0.35) 45%, rgba(220,205,180,0) 70%);
  }
  .card-title {
    position: absolute;
    top: 14px;
    left: 0;
    width: 848px;
    text-align: center;
    font-family: "Nunito", sans-serif;
    font-weight: 900;
    font-size: 49px;
    line-height: 1.1;
    color: var(--navy);
    text-shadow:
      2px 0 0 var(--halo), -2px 0 0 var(--halo), 0 2px 0 var(--halo), 0 -2px 0 var(--halo),
      2px 2px 0 var(--halo), -2px -2px 0 var(--halo), 2px -2px 0 var(--halo), -2px 2px 0 var(--halo);
  }
  .outcome-heading {
    position: absolute;
    top: 122px;
    left: 0;
    width: 848px;
    text-align: center;
    font-family: "Nunito", sans-serif;
    font-weight: 900;
    font-size: 33px;
    line-height: 46px;
    color: var(--navy);
    text-shadow:
      1.5px 0 0 var(--halo), -1.5px 0 0 var(--halo), 0 1.5px 0 var(--halo), 0 -1.5px 0 var(--halo),
      1.5px 1.5px 0 var(--halo), -1.5px -1.5px 0 var(--halo), 1.5px -1.5px 0 var(--halo), -1.5px 1.5px 0 var(--halo);
  }
  .prompt {
    position: absolute;
    left: 57px;
    font-family: "Open Sans", sans-serif;
    font-style: italic;
    font-weight: 800;
    font-size: 28.5px;
    line-height: 43px;
    color: var(--heading-blue);
  }
  .statement {
    position: absolute;
    left: 138px;
    font-family: "Didact Gothic", sans-serif;
    font-size: 37px;
    line-height: 46.5px;
    color: var(--ink);
  }
  .prompt--children { top: 277px; }
  .statement--children { top: 406px; }
  .prompt--educators { top: 597px; }
  .statement--educators { top: 686px; }
  .prompt--task { top: 813px; }
  .opportunity-list {
    position: absolute;
    top: 865px;
    left: 130px;
    list-style: none;
    font-family: "Didact Gothic", sans-serif;
    font-size: 29px;
    line-height: 41px;
    color: var(--ink);
  }
  .opportunity-list li {
    position: relative;
    padding-left: 33px;
  }
  .opportunity-list li::before {
    content: "";
    position: absolute;
    left: 2px;
    top: 13px;
    width: 15px;
    height: 15px;
    background: var(--diamond-red);
    transform: rotate(45deg);
  }
  .opportunity-list .continued { padding-left: 33px; }
  .opportunity-list .continued::before { display: none; }
</style>
</head>
<body>
<main class="task-card">
  <div class="beach-backdrop" role="img" aria-label="Photograph of a sandy beach with the sea behind and a stack of smooth white pebbles balanced on the sand"></div>
  <div class="stone-stack" aria-hidden="true"></div>

  <h1 class="card-title">2. Big Bigger Biggest</h1>

  <h2 class="outcome-heading">EYLF – Outcome 2: Children are<br>connected with and contribute<br>to their world</h2>

  <p class="prompt prompt--children">Children become socially responsible and<br>show respect for the environment when<br>they...</p>
  <p class="statement statement--children">explore relationships with other<br>living and non-living things and<br>observe, notice and respond to<br>change</p>

  <p class="prompt prompt--educators">Educators promote this learning when<br>they...</p>
  <p class="statement statement--educators">provide children with access to<br>a range of natural materials in<br>their environment</p>

  <p class="prompt prompt--task">This task provides an opportunity to:</p>
  <ul class="opportunity-list">
    <li>explore the concepts of “change” and</li>
    <li class="continued">“growth”</li>
    <li>discuss how growth happens</li>
    <li>make predictions about change</li>
    <li>formulate strategies for coping with</li>
    <li class="continued">change</li>
  </ul>
</main>
</body>
</html>
```